1876 Basins & Spouts Business Card

I'm wanting to get a business card designed. Our business is 1876 Basins & Spouts
Details for the card:

1876 Basins & Spouts
Name: Harold Vesk
Email: harold@1876basinsandspouts.com.au
Website: www.1876basinsandspouts.com.au
Mobile: 0438 260 947
Phone: 02 7481 3926

Font of Basins & Spouts is called Snell Roundhand. Not sue what font logo text is.

I'm thinking two sided but it doesn't have to be.

```html
<!DOCTYPE html>
<html lang="en">
<head>
<meta charset="utf-8">
<title>1876 Basins &amp; Spouts Business Card</title>
<link rel="stylesheet" href="https://fonts.googleapis.com/css2?family=Lato:wght@400;700&family=Montserrat:wght@700&display=swap">
<style>
  :root {
    --canvas: #3a3d42;
    --card-black: #050505;
    --card-white: #ffffff;
    --ink-white: #ffffff;
    --ink-black: #0a0a0a;
    --grey-light: #c9c9cc;
    --grey-mid: #8c8c90;
    --grey-dark: #4a4a4e;
  }
  * { box-sizing: border-box; margin: 0; padding: 0; }
  html, body {
    width: 1200px; height: 1000px; overflow: hidden;
    background: var(--canvas);
    font-family: "Lato", sans-serif;
  }
  .sheet {
    position: relative; width: 1200px; height: 1000px;
    display: flex; flex-direction: column; align-items: center;
    justify-content: center; gap: 36px;
  }
  .card {
    position: relative; width: 780px; height: 446px;
    border-radius: 22px; overflow: hidden;
    background: var(--card-black);
  }

  /* Front */
  .front-logo {
    position: absolute; left: 0; right: 0; top: 150px;
    display: flex; align-items: center; justify-content: center; gap: 16px;
    color: var(--ink-white);
  }
  .logo-dot {
    width: 18px; height: 18px; border-radius: 50%;
    border: 2px solid currentColor;
  }
  .logo-name {
    font-family: "Lato", sans-serif; font-weight: 400;
    font-size: 38px; letter-spacing: 0.5px; white-space: nowrap;
  }
  .tagline {
    position: absolute; left: 0; right: 0; top: 214px;
    text-align: center; color: var(--ink-white);
    font-size: 17px; letter-spacing: 0.6px;
  }
  .front-company {
    position: absolute; left: 0; right: 0; bottom: 62px;
    text-align: center; color: var(--ink-white);
    font-size: 19px; letter-spacing: 0.4px;
  }

  /* Back */
  .back-shape { position: absolute; inset: 0; }
  .back-logo {
    position: absolute; left: 20px; top: 200px; width: 350px;
    display: flex; align-items: center; justify-content: center; gap: 10px;
    color: var(--ink-black);
  }
  .back-logo .logo-name { font-size: 25px; }
  .back-logo .logo-dot { width: 13px; height: 13px; }
  .holder {
    position: absolute; right: 70px; top: 160px;
    text-align: right; color: var(--ink-white);
  }
  .holder-name {
    font-family: "Montserrat", sans-serif; font-weight: 700;
    font-size: 38px; letter-spacing: 0.5px; white-space: nowrap;
  }
  .holder-rule {
    width: 30px; height: 4px; background: var(--ink-white);
    margin: 30px 0 0 auto;
  }
  .contacts {
    position: absolute; right: 44px; top: 286px;
    list-style: none; color: var(--ink-white);
  }
  .contacts li {
    display: flex; align-items: center; justify-content: flex-end;
    gap: 16px; font-size: 19px; line-height: 32px; white-space: nowrap;
  }
  .contacts svg { width: 18px; height: 18px; flex: none; }
</style>
</head>
<body>
<main class="sheet">

  <section class="card front" aria-label="Card front">
    <div class="front-logo">
      <span class="logo-dot"></span>
      <span class="logo-name">1876 Basins &amp; Spouts</span>
    </div>
    <p class="tagline">Combining timeless beauty with perfect practicality</p>
    <p class="front-company">1876 Basins &amp; Spouts</p>
  </section>

  <section class="card back" aria-label="Card back">
    <svg class="back-shape" viewBox="0 0 780 446" width="780" height="446" aria-hidden="true">
      <defs>
        <linearGradient id="band-outer" x1="0" y1="1" x2="1" y2="0">
          <stop offset="0" stop-color="var(--grey-light)"/>
          <stop offset="0.6" stop-color="var(--grey-mid)"/>
          <stop offset="1" stop-color="var(--grey-dark)"/>
        </linearGradient>
        <linearGradient id="band-inner" x1="0" y1="0" x2="0" y2="1">
          <stop offset="0" stop-color="var(--grey-mid)"/>
          <stop offset="0.5" stop-color="var(--grey-light)"/>
          <stop offset="1" stop-color="var(--grey-dark)"/>
        </linearGradient>
      </defs>
      <path d="M414,0 H424 C464,120 464,320 234,446 H224 C454,320 454,120 414,0 Z" fill="url(#band-inner)"/>
      <path d="M392,0 H406 C446,120 446,320 216,446 H202 C432,320 432,120 392,0 Z" fill="url(#band-outer)"/>
      <path d="M0,0 H380 C420,120 420,320 190,446 H0 Z" fill="var(--card-white)"/>
    </svg>

    <div class="back-logo">
      <span class="logo-dot"></span>
      <span class="logo-name">1876 Basins &amp; Spouts</span>
    </div>

    <div class="holder">
      <h1 class="holder-name">Harold Vesk</h1>
      <div class="holder-rule"></div>
    </div>

    <ul class="contacts">
      <li>02 7481 3926
        <svg viewBox="0 0 24 24" aria-label="Phone"><path fill="#fff" d="M6.6 10.8a15 15 0 0 0 6.6 6.6l2.2-2.2a1 1 0 0 1 1-.25 11.4 11.4 0 0 0 3.6.6 1 1 0 0 1 1 1V20a1 1 0 0 1-1 1A17 17 0 0 1 3 4a1 1 0 0 1 1-1h3.5a1 1 0 0 1 1 1c0 1.25.2 2.450.6 3.6a1 1 0 0 1-.25 1z"/></svg>
      </li>
      <li>0438 260 947
        <svg viewBox="0 0 24 24" aria-label="Mobile"><rect x="6" y="2" width="12" height="20" rx="2" fill="none" stroke="#fff" stroke-width="2"/><circle cx="12" cy="18" r="1.2" fill="#fff"/></svg>
      </li>
      <li>harold@1876basinsandspouts.com.au
        <svg viewBox="0 0 24 24" aria-label="Email"><rect x="2" y="5" width="20" height="14" rx="1.5" fill="#fff"/><path d="M3 6l9 7 9-7" fill="none" stroke="#050505" stroke-width="2"/></svg>
      </li>
      <li>www.1876basinsandspouts.com.au
        <svg viewBox="0 0 24 24" aria-label="Website"><circle cx="12" cy="12" r="10" fill="#fff"/><path d="M2 12h20M12 2c3 3 3 17 0 20M12 2c-3 3-3 17 0 20" fill="none" stroke="#050505" stroke-width="1.5"/></svg>
      </li>
    </ul>
  </section>

</main>
</body>
</html>
```